Half page (a5) ad for a company

I need a design for an ad for a company to be published in a conference catalogue. Please find enclosed the logo for a company. The company is providing health screening services. Ad should be subtle and minimalistic, i.e. logo in the centre and a phrase saying: "Be in charge of your own health" and the website bluefen.co.uk. Also please find enclosed guidlines for colours and fonts to be used.

```html
<!DOCTYPE html>
<html lang="en">
<head>
<meta charset="utf-8">
<title>Bluefen Private – Half Page Ad</title>
<link rel="stylesheet" href="https://fonts.googleapis.com/css2?family=Montserrat:ital,wght@0,300;0,400;0,600;1,300&display=swap">
<style>
  :root {
    --brand-red: #e31e26;
    --ink-grey: #666666;
    --url-grey: #777777;
    --frame-grey: #4a4a4a;
    --paper: #ffffff;
    --shadow: rgba(60, 60, 60, 0.55);
    --hair-dark: #2e221d;
    --skin-warm: #c48a68;
    --legging-red: #d61f2b;
  }
  * { box-sizing: border-box; margin: 0; padding: 0; }
  html, body {
    width: 846px;
    height: 1200px;
    overflow: hidden;
    background: var(--paper);
  }
  .ad {
    position: relative;
    width: 846px;
    height: 1200px;
    background: var(--paper);
    border: 1px solid var(--frame-grey);
    font-family: "Montserrat", Arial, sans-serif;
  }
  .brand {
    position: absolute;
    top: 74px;
    left: 0;
    width: 100%;
    text-align: center;
  }
  .brand__dot {
    display: block;
    width: 64px;
    height: 64px;
    margin: 0 auto 38px;
    border-radius: 50%;
    background: var(--brand-red);
  }
  .brand__name {
    font-weight: 400;
    font-size: 36px;
    letter-spacing: 0.5px;
    color: var(--brand-red);
    line-height: 1;
  }
  .hero-photo {
    position: absolute;
    left: 308px;
    top: 390px;
    width: 196px;
    height: 560px;
    border-radius: 90px 90px 40px 40px;
    background: linear-gradient(to bottom,
      var(--hair-dark) 0%,
      var(--skin-warm) 28%,
      var(--skin-warm) 42%,
      var(--legging-red) 58%,
      var(--legging-red) 100%);
  }
  .hero-shadow {
    position: absolute;
    left: 0;
    top: 955px;
    width: 100%;
    height: 30px;
  }
  .tagline {
    position: absolute;
    top: 1040px;
    left: 0;
    width: 100%;
    text-align: center;
    font-size: 27px;
    color: var(--ink-grey);
    letter-spacing: -0.8px;
  }
  .tagline__strong { font-weight: 600; }
  .tagline__soft { font-weight: 300; font-style: italic; }
  .website {
    position: absolute;
    top: 1128px;
    left: 0;
    width: 100%;
    text-align: center;
    font-weight: 300;
    font-size: 18px;
    letter-spacing: 3.5px;
    color: var(--url-grey);
  }
</style>
</head>
<body>
  <main class="ad">
    <header class="brand">
      <span class="brand__dot"></span>
      <p class="brand__name">Bluefen Private</p>
    </header>

    <div class="hero-photo" role="img" aria-label="Photo of a young woman with curly hair jogging towards the viewer in a black sports top, red leggings and white trainers"></div>

    <svg class="hero-shadow" viewBox="0 0 846 30" aria-hidden="true">
      <defs>
        <radialGradient id="ground-shadow" cx="50%" cy="50%" r="50%">
          <stop offset="0%" stop-color="var(--shadow)"/>
          <stop offset="100%" stop-color="rgba(60,60,60,0)"/>
        </radialGradient>
      </defs>
      <ellipse cx="438" cy="15" rx="80" ry="9" fill="url(#ground-shadow)"/>
    </svg>

    <p class="tagline"><span class="tagline__strong">Be incharge of</span> <span class="tagline__soft">your own health</span></p>

    <p class="website">www.bluefen.co.uk.</p>
  </main>
</body>
</html>
```